Website for IT consulting Company

I need a website upgrade, the existing site content is ok, I would also like to add a testimonial page, the site should be something that is easy for us to update content. You use the content from www.kelvanbrook.com as an example. I will also post update logo and artwork. I also need a contact form with some type of validation or captcha.

I added Coded to the Project

Please omit Address maps

Target Market(s)

small business, service oriented companies. We provide IT Consulting, support and mangement

Industry/Entity Type

Information Technology

Coding

Number of Pages Required

1 page

Font styles to use
Serif
Sans Serif

Requirements
Must have
• Contain logo attached, and content from existing web site www.kelvanbrook.com.
• Also need to update content easily, and be movable to different platforms.
• There is a catch phrase
• "Let us worry about your technology…” “ so you don’t have to!”
• Should be included.
Nice to have
• Testimonial page, Project page where we can post new and past projects and pictures
Should not have
• none

```html
<!DOCTYPE html>
<html lang="en">
<head>
<meta charset="utf-8">
<title>Kelvanbrook Development Group – IT Solutions</title>
<link href="https://fonts.googleapis.com/css2?family=Exo+2:wght@300;400;500;600;700&family=Roboto:wght@300;400;500&display=swap" rel="stylesheet">
<style>
:root{
  --blue:#1a7ac4;
  --blue-dark:#125f9e;
  --blue-light:#3a9be0;
  --ink:#222;
  --muted:#888;
  --grey-bg:#f2f2f2;
  --line:#e2e2e2;
  --white:#fff;
}
*{box-sizing:border-box;margin:0;padding:0}
html,body{width:1200px;height:3175px;overflow:hidden}
body{position:relative;font-family:"Roboto",Arial,sans-serif;color:var(--ink);background:var(--white)}
.section{position:absolute;left:0;width:1200px}
h2.section-title{font-family:"Exo 2",Arial,sans-serif;font-weight:400;font-size:40px;text-align:center;letter-spacing:1px;color:var(--ink)}

/* top bar */
.topbar{top:0;height:40px;background:var(--blue)}
.topbar .social{position:absolute;left:82px;top:0;display:flex}
.topbar .social span{width:40px;height:40px;border-right:1px solid rgba(255,255,255,.3);display:flex;align-items:center;justify-content:center}
.topbar .social span i{width:12px;height:12px;background:var(--white);display:block;border-radius:2px}
.topbar .phone{position:absolute;right:82px;top:10px;color:var(--white);font-size:16px;display:flex;gap:8px;align-items:center}

/* header */
.header{top:40px;height:108px;background:var(--white)}
.brand{position:absolute;left:78px;top:22px}
.brand-name{display:flex;align-items:center;gap:10px;font-family:"Exo 2",sans-serif;font-weight:700;font-size:40px;color:var(--blue-dark)}
.brand-name b{width:34px;height:34px;background:var(--blue);display:block}
.brand-tag{font-size:9px;color:var(--blue);margin-top:2px;margin-left:44px}
.nav{position:absolute;right:82px;top:44px;display:flex;gap:30px;font-size:16px;color:#444}
.nav a{text-decoration:none;color:inherit;display:flex;align-items:center;gap:6px}
.nav a i{width:12px;height:12px;background:#666;transform:rotate(45deg);display:block}
.nav a.active{color:var(--blue)}
.nav a.active i{background:var(--blue)}

/* hero */
.hero{top:148px;height:572px;overflow:hidden}
.hero-scene{position:absolute;inset:0;background:linear-gradient(180deg,#f4f4f4 0%,#e9e9e9 52%,#8a7f76 62%,#5a524c 100%)}
.hero-laptop{position:absolute;left:545px;top:195px;width:475px;height:300px;background:linear-gradient(180deg,#dfe7ef,#b8c4ce);border-radius:10px}
.hero-copy{position:absolute;left:80px;top:96px}
.hero-title{font-family:"Exo 2",sans-serif;font-weight:600;color:var(--blue);font-size:44px;line-height:66px}
.hero-title strong{font-size:68px;font-weight:700}
.hero-sub{font-size:24px;color:#222;margin-top:2px}
.btn{display:inline-flex;align-items:center;height:50px;font-size:17px;text-transform:uppercase;text-decoration:none}
.btn span{padding:0 28px}
.btn b{width:50px;height:50px;background:#111;display:flex;align-items:center;justify-content:center}
.btn b i{width:18px;height:18px;background:var(--blue-light);display:block}
.btn-blue{background:var(--blue);color:var(--white)}
.btn-white{background:var(--white);color:#222}
.hero .btn{margin-top:28px}
.arrow-nav{position:absolute;font-size:44px;color:#111;font-family:"Roboto",sans-serif}
.dots{position:absolute;left:0;width:100%;display:flex;justify-content:center;gap:6px}
.dots i{width:14px;height:14px;border-radius:50%;border:2px solid #555;background:var(--white);display:block}
.dots i.on{background:var(--blue);border-color:var(--blue)}

/* services */
.services{top:720px;height:380px;background:var(--grey-bg)}
.services .intro{width:720px;margin:18px auto 0;text-align:center;font-size:14px;line-height:26px;color:#444}
.tabs{position:absolute;left:80px;top:170px;width:1040px;height:155px;background:var(--white);border:1px solid var(--line);display:flex}
.tab{flex:1;display:flex;flex-direction:column;align-items:center;justify-content:flex-end;padding-bottom:26px;gap:22px;font-size:15px;color:#555;border-right:1px solid var(--line)}
.tab:last-child{border-right:none}
.tab.active{color:var(--blue);border-bottom:3px solid var(--blue);font-size:17px}

/* about */
.about{top:1100px;height:290px;background:var(--blue)}
.about-left{position:absolute;left:0;top:0;width:415px;height:290px;background:var(--blue-light)}
.about-left h2{position:absolute;left:80px;top:120px;font-family:"Exo 2",sans-serif;font-weight:400;font-size:40px;color:#111}
.about-mark{position:absolute;left:150px;top:40px;width:160px;height:160px;background:rgba(255,255,255,.08)}
.about-right{position:absolute;left:448px;top:52px;width:680px;font-size:14px;line-height:23px;color:rgba(255,255,255,.85)}
.about-right .btn{margin-top:22px}

/* support */
.support{top:1390px;height:472px;background:var(--white)}
.support h2{padding-top:50px}
.cards{position:absolute;left:80px;top:117px;width:1040px;display:flex;justify-content:space-between}
.card{width:254px;height:303px;text-align:center;padding-top:30px}
.card.active{box-shadow:0 4px 22px rgba(0,0,0,.22)}
.card-icon{width:92px;height:92px;margin:0 auto;border:2px solid var(--blue);border-radius:8px;display:flex;align-items:center;justify-content:center}
.card.active .card-icon{background:var(--blue)}
.card h3{font-weight:400;font-size:16px;margin-top:24px;color:#222;text-transform:uppercase}
.card.active h3{color:var(--blue)}
.card p{font-size:14px;line-height:23px;color:var(--muted);margin:10px 22px 0}
.card a{display:inline-block;margin-top:12px;font-size:14px;color:#333;text-decoration:underline}
.support .arrow-nav{top:160px}

/* outsourcing */
.outsourcing{top:1862px;height:518px;overflow:hidden}
.out-scene{position:absolute;inset:0;background:linear-gradient(180deg,#3a3f44 0%,#5a6168 45%,#3a4046 100%)}
.outsourcing h2{position:relative;padding-top:44px;color:var(--white)}
.flow-line{position:absolute;height:12px;background:var(--blue-light)}
.flow-icon{position:absolute;width:126px;height:126px;background:var(--white);border:3px solid var(--blue);border-radius:6px;display:flex;align-items:center;justify-content:center}
.flow-icon.filled{background:var(--blue);border-color:var(--white)}
.flow-label{position:absolute;height:72px;background:var(--blue);border:2px solid #7cc0f0;color:var(--white);font-size:25px;display:flex;align-items:center;justify-content:center;gap:10px;font-family:"Roboto",sans-serif}
.flow-label.link{text-decoration:underline}
.flow-label i{font-style:normal;width:16px;height:16px;border-radius:50%;background:var(--white);color:var(--blue);font-size:11px;line-height:16px;text-align:center;text-decoration:none}
.wave{position:absolute;left:0;bottom:0;width:1200px;height:40px}

/* testimonial */
.testimonial{top:2380px;height:350px;background:var(--grey-bg)}
.testimonial h2{padding-top:40px}
.quote{position:absolute;top:118px;width:500px}
.quote .photo{position:absolute;left:0;top:32px;width:102px;height:102px;border:4px solid var(--white);box-shadow:0 0 0 1px #ccc}
.quote .who{position:absolute;left:130px;top:0;font-size:18px}
.quote .text{position:absolute;left:130px;top:34px;width:330px;font-size:17px;line-height:21px;color:#444}
.quote .text b{color:#a9c8e6;font-size:26px;font-weight:700}
.testimonial .dots{top:285px}

/* contact */
.contact{top:2730px;height:445px;background:linear-gradient(180deg,#1b7ed0 0%,#1570bb 60%,#1466ac 100%);color:var(--white)}
.contact-scene{position:absolute;left:0;top:120px;width:1200px;height:260px;background:linear-gradient(180deg,rgba(255,255,255,0),rgba(255,255,255,.08))}
.contact h2{position:relative;padding-top:45px;color:var(--white)}
.contact-info{position:absolute;top:120px;left:0;width:1200px;font-size:14px;line-height:23px;color:rgba(255,255,255,.85)}
.contact-info div{position:absolute;display:flex;gap:12px}
.follow,.subscribe{position:absolute;top:250px;font-size:15px;text-transform:uppercase;text-align:center}
.follow{left:300px;width:190px}
.follow .squares{display:flex;gap:8px;justify-content:center;margin-top:20px}
.follow .squares i{width:32px;height:32px;background:#111;display:block}
.subscribe{left:670px;width:220px}
.subscribe .field{margin-top:18px;height:36px;background:var(--blue-light);border:1px solid #5fb0ee;display:flex;align-items:center;justify-content:space-between;padding:0 10px;font-size:13px;text-transform:none;color:var(--white)}
.copyright{position:absolute;left:0;bottom:10px;width:1200px;text-align:center;font-size:15px;color:rgba(255,255,255,.9)}
</style>
</head>
<body>

<div class="section topbar">
  <div class="social"><span><i></i></span><span><i></i></span><span><i></i></span></div>
  <div class="phone">
    <svg width="16" height="16" viewBox="0 0 24 24"><path fill="#fff" d="M6.6 10.8a15 15 0 0 0 6.6 6.6l2.2-2.2c.3-.3.7-.4 1-.2 1.1.4 2.3.6 3.6.6.6 0 1 .4 1 1V20c0 .6-.4 1-1 1A17 17 0 0 1 3 4c0-.6.4-1 1-1h3.5c.6 0 1 .4 1 1 0 1.3.2 2.5.6 3.6.1.3 0 .7-.2 1z"/></svg>
    (713) 555-0148
  </div>
</div>

<header class="section header">
  <div class="brand">
    <div class="brand-name"><b></b>KELVANBROOK</div>
    <div class="brand-tag">Leave the tech side to us… and focus on your work!</div>
  </div>
  <nav class="nav">
    <a class="active" href="#"><i></i>Home</a>
    <a href="#"><i></i>About</a>
    <a href="#"><i></i>Support</a>
    <a href="#"><i></i>Clients</a>
    <a href="#"><i></i>Careers</a>
    <a href="#"><i></i>Contact us</a>
  </nav>
</header>

<section class="section hero">
  <div class="hero-scene" role="img" aria-label="Photo of a laptop and a potted plant on a wooden desk against a white brick wall"></div>
  <div class="hero-laptop" role="img" aria-label="Laptop showing the website"></div>
  <div class="hero-copy">
    <div class="hero-title">IT solutions that <strong>WORK</strong><br>for <strong>YOUR</strong> business.</div>
    <div class="hero-sub">A full service technology company</div>
    <a class="btn btn-blue" href="#"><span>Read more</span><b><i></i></b></a>
  </div>
  <div class="arrow-nav" style="left:22px;top:238px">«</div>
  <div class="arrow-nav" style="right:22px;top:238px">»</div>
  <div class="dots" style="top:549px"><i class="on"></i><i></i><i></i><i></i></div>
</section>

<section class="section services">
  <h2 class="section-title" style="padding-top:48px">OUR SERVICES</h2>
  <p class="intro">Find out just how to make the best out of the assets you have at your disposal &amp; become one of the leading companies in the up-and-coming market of today.Our Best Solution Are :</p>
  <div class="tabs">
    <div class="tab active">
      <svg width="84" height="50" viewBox="0 0 84 50"><path d="M8 32a10 10 0 0 1 8-16 14 14 0 0 1 26 2 8 8 0 0 1 2 14z" fill="#222"/><rect x="36" y="18" width="40" height="26" fill="none" stroke="#222" stroke-width="3"/><circle cx="56" cy="31" r="6" fill="none" stroke="#1a7ac4" stroke-width="3"/></svg>
      Managed IT Solutions
    </div>
    <div class="tab">
      <svg width="210" height="56" viewBox="0 0 210 56"><circle cx="26" cy="28" r="24" fill="#1a7ac4"/><circle cx="26" cy="28" r="11" fill="none" stroke="#fff" stroke-width="3"/><line x1="52" y1="28" x2="150" y2="28" stroke="#aaa" stroke-width="2"/><rect x="92" y="18" width="20" height="20" fill="#1a7ac4"/><rect x="150" y="8" width="52" height="36" fill="none" stroke="#222" stroke-width="3"/><line x1="168" y1="50" x2="184" y2="50" stroke="#222" stroke-width="3"/></svg>
      Remote Diagnostic and Support
    </div>
    <div class="tab">
      <svg width="110" height="66" viewBox="0 0 110 66"><rect x="2" y="6" width="56" height="38" fill="none" stroke="#222" stroke-width="3"/><rect x="12" y="14" width="16" height="14" fill="#1a7ac4"/><rect x="86" y="18" width="20" height="34" rx="3" fill="#1a7ac4"/><circle cx="72" cy="30" r="5" fill="#222"/><path d="M30 44v14h60" fill="none" stroke="#1a7ac4" stroke-width="2"/></svg>
      IT Infrastructure Design and Installation
    </div>
  </div>
</section>

<section class="section about">
  <div class="about-left">
    <div class="about-mark"></div>
    <h2>ABOUT US</h2>
  </div>
  <div class="about-right">
    <p>Kelvanbrook Development Group, Inc. was established in 1991. Our mission is helping businesses and individuals realize a Return on Investment by implementing today's advanced technologies. As a small business we understand the importance of technology and personalized attention.Every member of our support team has worked with both large and small companies supporting a multitude of applications, networks and environments.</p>
    <a class="btn btn-white" href="#"><span>Read more</span><b><i></i></b></a>
  </div>
</section>

<section class="section support">
  <h2 class="section-title">IT SUPPORT SOLUTIONS</h2>
  <div class="arrow-nav" style="left:22px">«</div>
  <div class="arrow-nav" style="right:22px">»</div>
  <div class="cards">
    <div class="card">
      <div class="card-icon"><svg width="52" height="44" viewBox="0 0 52 44"><path d="M8 30a8 8 0 0 1 6-14 12 12 0 0 1 23 2 7 7 0 0 1 3 12z" fill="none" stroke="#333" stroke-width="2"/><rect x="28" y="22" width="4" height="10" fill="#333"/><rect x="34" y="18" width="4" height="14" fill="#333"/><rect x="40" y="14" width="4" height="18" fill="#333"/></svg></div>
      <h3>Network Administration</h3>
      <p>Lorem Ipsum is simply dummy text of the printing and typesetting industry.</p>
      <a href="#">LEARN MORE</a>
    </div>
    <div class="card">
      <div class="card-icon"><svg width="52" height="44" viewBox="0 0 52 44"><rect x="4" y="4" width="34" height="24" fill="none" stroke="#333" stroke-width="2"/><rect x="14" y="14" width="34" height="24" fill="#fff" stroke="#333" stroke-width="2"/><rect x="20" y="20" width="12" height="8" fill="#1a7ac4"/></svg></div>
      <h3>Desktop Support</h3>
      <p>Lorem Ipsum is simply dummy text of the printing and typesetting industry.</p>
      <a href="#">LEARN MORE</a>
    </div>
    <div class="card active">
      <div class="card-icon"><svg width="52" height="52" viewBox="0 0 52 52"><path d="M10 42 40 12" stroke="#fff" stroke-width="6"/><circle cx="14" cy="16" r="8" fill="none" stroke="#fff" stroke-width="3"/><rect x="34" y="30" width="12" height="14" fill="none" stroke="#fff" stroke-width="3"/></svg></div>
      <h3>Network Cabling</h3>
      <p>Lorem Ipsum is simply dummy text of the printing and typesetting industry.</p>
      <a href="#" style="color:#1a7ac4">LEARN MORE</a>
    </div>
    <div class="card">
      <div class="card-icon"><svg width="52" height="52" viewBox="0 0 52 52"><circle cx="26" cy="20" r="4" fill="#333"/><line x1="26" y1="24" x2="26" y2="46" stroke="#333" stroke-width="3"/><path d="M16 10a14 14 0 0 0 0 20M36 10a14 14 0 0 1 0 20M10 4a22 22 0 0 0 0 32M42 4a22 22 0 0 1 0 32" fill="none" stroke="#333" stroke-width="2"/></svg></div>
      <h3>Wireless Network</h3>
      <p>Lorem Ipsum is simply dummy text of the printing and typesetting industry.</p>
      <a href="#">LEARN MORE</a>
    </div>
  </div>
</section>

<section class="section outsourcing">
  <div class="out-scene" role="img" aria-label="Dimmed photo of an office interior with desks and computers"></div>
  <h2 class="section-title">OUTSOURCING TECHNOLOGY</h2>
  <div class="flow-line" style="left:226px;top:205px;width:870px"></div>
  <div class="flow-line" style="left:95px;top:362px;width:1003px"></div>

  <div class="flow-icon filled" style="left:100px;top:148px"><svg width="60" height="56" viewBox="0 0 60 56"><rect x="8" y="10" width="44" height="30" fill="none" stroke="#fff" stroke-width="3"/><circle cx="30" cy="25" r="7" fill="none" stroke="#fff" stroke-width="3"/><line x1="4" y1="48" x2="56" y2="48" stroke="#fff" stroke-width="3"/></svg></div>
  <div class="flow-label link" style="left:271px;top:176px;width:311px"><i>‹</i>Technology</div>
  <div class="flow-icon" style="left:624px;top:148px"><svg width="64" height="64" viewBox="0 0 64 64"><circle cx="32" cy="32" r="8" fill="#1a7ac4"/><circle cx="10" cy="14" r="6" fill="#1a7ac4"/><circle cx="54" cy="14" r="6" fill="#1a7ac4"/><circle cx="10" cy="50" r="6" fill="#1a7ac4"/><circle cx="54" cy="50" r="6" fill="#1a7ac4"/><path d="M10 14 32 32 54 14M10 50 32 32 54 50M10 14h44M10 50h44" stroke="#1a7ac4" stroke-width="2" fill="none"/></svg></div>
  <div class="flow-label" style="left:791px;top:176px;width:309px"><i>‹</i>Outsourcing</div>

  <div class="flow-label" style="left:95px;top:332px;width:311px">Growth<i>›</i></div>
  <div class="flow-icon" style="left:449px;top:305px"><svg width="64" height="56" viewBox="0 0 64 56"><rect x="6" y="36" width="8" height="16" fill="#1a7ac4"/><rect x="20" y="28" width="8" height="24" fill="#1a7ac4"/><rect x="34" y="20" width="8" height="32" fill="#1a7ac4"/><rect x="48" y="12" width="8" height="40" fill="#1a7ac4"/><path d="M4 28 24 12l12 8L58 2" stroke="#1a7ac4" stroke-width="3" fill="none"/></svg></div>
  <div class="flow-label" style="left:616px;top:332px;width:313px">Commitments<i>›</i></div>
  <div class="flow-icon" style="left:973px;top:305px"><svg width="70" height="44" viewBox="0 0 70 44"><path d="M2 10h14l14 10 10-8h12l16 10M16 10v20l14 10 8-4 8 4 10-8h12" stroke="#1a7ac4" stroke-width="4" fill="none"/></svg></div>

  <svg class="wave" viewBox="0 0 1200 40" preserveAspectRatio="none"><path d="M0 40V34h520c40 0 50-30 80-30s40 30 80 30h520v6z" fill="#f2f2f2"/><path d="M592 14l8 6 8-6M592 22l8 6 8-6" stroke="#1a7ac4" stroke-width="2" fill="none"/></svg>
</section>

<section class="section testimonial">
  <h2 class="section-title">TESTIMONIAL</h2>
  <div class="quote" style="left:112px">
    <div class="photo" role="img" aria-label="Portrait photo of a client" style="background:linear-gradient(160deg,#e8d3bf,#b99b83)"></div>
    <div class="who">- Dana , Elm Ridge,NJ</div>
    <div class="text"><b>“</b> "Lorem Ipsum is simply dummy text of the printing and typesetting industry. Lorem Ipsum has been the industry's standard dummy text ever since the 1500."</div>
  </div>
  <div class="quote" style="left:648px">
    <div class="photo" role="img" aria-label="Portrait photo of a client" style="background:linear-gradient(160deg,#dfe6ee,#7d93ab)"></div>
    <div class="who">- Dana , Elm Ridge,NJ</div>
    <div class="text"><b>“</b> "Lorem Ipsum is simply dummy text of the printing and typesetting industry. Lorem Ipsum has been the industry's standard dummy text ever since the 1500."</div>
  </div>
  <div class="dots"><i class="on"></i><i></i><i></i><i></i></div>
</section>

<footer class="section contact">
  <div class="contact-scene" role="img" aria-label="Faint city skyline photo in blue tones"></div>
  <h2 class="section-title">CONTACT US</h2>
  <div class="contact-info">
    <div style="left:276px;top:0">
      <svg width="14" height="20" viewBox="0 0 14 20"><path d="M7 0a7 7 0 0 1 7 7c0 5-7 13-7 13S0 12 0 7a7 7 0 0 1 7-7z" fill="none" stroke="#fff" stroke-width="1.5"/><circle cx="7" cy="7" r="2.5" fill="#fff"/></svg>
      <span>Kelvanbrook Development Group, Inc.<br>1418 Marlow St.<br>Calderwood, Texas 75099</span>
    </div>
    <div style="left:553px;top:0">
      <svg width="18" height="18" viewBox="0 0 24 24"><path fill="none" stroke="#fff" stroke-width="1.6" d="M6.6 10.8a15 15 0 0 0 6.6 6.6l2.2-2.2c.3-.3.7-.4 1-.2 1.1.4 2.3.6 3.6.6.6 0 1 .4 1 1V20c0 .6-.4 1-1 1A17 17 0 0 1 3 4c0-.6.4-1 1-1h3.5c.6 0 1 .4 1 1 0 1.3.2 2.5.6 3.6.1.3 0 .7-.2 1z"/></svg>
      <span>(713) 555-0148</span>
    </div>
    <div style="left:755px;top:0">
      <svg width="18" height="18" viewBox="0 0 20 20"><path d="M1 9 19 1l-6 18-3-7z" fill="none" stroke="#fff" stroke-width="1.5"/></svg>
      <span>info@kelvanbrook.com</span>
    </div>
  </div>
  <div class="follow">Follow us on
    <div class="squares"><i></i><i></i><i></i></div>
  </div>
  <div class="subscribe">Subscribe here
    <div class="field"><span>✉ Email</span><svg width="18" height="18" viewBox="0 0 20 20"><path d="M1 9 19 1l-6 18-3-7z" fill="none" stroke="#fff" stroke-width="1.5"/></svg></div>
  </div>
  <div class="copyright">© <strong>Kelvanbrook Development Group,Inc.</strong> - 2017 All Right Reserved</div>
</footer>

</body>
</html>
```